Chocolate Bar Design

I need packaging design for a new line of chocolate bars.

The new design must fit in with the packaging design for our line of solid chocolate bars. The previous bars are packaged in clear boxes, the new line is in 3x3 kraft boxes so the new design must be visusally appealing, and portray what lies inside as they are not able to view the bar itself.

The new product line is for "Truffle Bars", basically a chocolate bar with a truffle filling. The first three flavors are Velmora Ember (Cinnamon and Cayenne, Sea Salt), Cafe Mocha, and Pumpkin Pie.

These are artisan bars, and should reflect in the packaging.

If you view our previous packaging, they are the same design but with a different color for each flavor, which would be ideal.

Industry/Entity Type

Cafe

Requirements
Must have
• Each design should include the front label that has the company name, size of the bar, and name of the bar at minimum. The reverse label must have company name, address, website, and ingredients, at minimum.

Nice to have
• Ideally, I would be able to edit ingredients, and bar names easily.

```html
<!DOCTYPE html>
<html lang="en">
<head>
<meta charset="utf-8">
<title>Truffle Bar Labels</title>
<link rel="stylesheet" href="https://fonts.googleapis.com/css2?family=Gelasio:wght@400;700&family=Roboto+Condensed:wght@400&display=swap">
<style>
  :root {
    --gold: #c2a25f;
    --card: #ffffff;
    --ink: #1c1a19;
    --cream-text: #ffffff;
    --mocha-band: #9b6c4f;
    --mocha-title: #6b3a24;
    --ember-band: #b3593a;
    --ember-title: #7f2a12;
    --pumpkin-band: #ee6f2c;
    --pumpkin-title: #e0412c;
    --bar-light: #8a5a4a;
    --bar-dark: #4a2a22;
  }
  * { box-sizing: border-box; margin: 0; padding: 0; }
  html, body {
    width: 1200px;
    height: 427px;
    overflow: hidden;
    background: #ffffff;
  }
  .label-sheet {
    position: relative;
    width: 1200px;
    height: 427px;
  }
  .label {
    position: absolute;
    top: 27px;
    width: 370px;
    height: 370px;
    background: var(--gold);
  }
  .label--mocha { left: 27px; --band: var(--mocha-band); --title: var(--mocha-title); }
  .label--ember { left: 416px; --band: var(--ember-band); --title: var(--ember-title); }
  .label--pumpkin { left: 805px; --band: var(--pumpkin-band); --title: var(--pumpkin-title); }

  .label__card {
    position: absolute;
    left: 31px;
    top: 31px;
    width: 309px;
    height: 309px;
    background: var(--card);
    border-radius: 22px;
    overflow: hidden;
  }
  .brand {
    position: absolute;
    top: 26px;
    left: 0;
    width: 100%;
    text-align: center;
    font-family: "Gelasio", Georgia, serif;
    font-weight: 400;
    color: var(--ink);
    line-height: 1;
  }
  .brand__name {
    display: block;
    font-size: 38px;
    letter-spacing: 0.5px;
  }
  .brand__line {
    display: block;
    margin-top: 8px;
    padding-left: 70px;
    font-size: 17px;
    letter-spacing: 5px;
  }
  .flavour-band {
    position: absolute;
    left: 0;
    top: 114px;
    width: 100%;
    height: 126px;
    background: var(--band);
  }
  .flavour-name {
    position: absolute;
    z-index: 3;
    left: 0;
    top: 0;
    height: 52px;
    background: var(--title);
    color: var(--gold);
    font-family: "Gelasio", Georgia, serif;
    font-weight: 700;
    font-size: 26px;
    line-height: 52px;
    padding: 0 12px 0 13px;
    white-space: nowrap;
  }
  .flavour-desc {
    position: absolute;
    left: 13px;
    top: 63px;
    color: var(--cream-text);
    font-family: "Roboto Condensed", "Arial Narrow", sans-serif;
    font-size: 15.5px;
    line-height: 20px;
  }
  .bar-visual {
    position: absolute;
    z-index: 2;
    left: 155px;
    top: 130px;
    width: 154px;
    height: 179px;
    background: linear-gradient(135deg, var(--bar-light) 0%, #6e4236 55%, var(--bar-dark) 100%);
    clip-path: polygon(90px 0, 154px 15px, 154px 179px, 45px 179px, 10px 100px);
  }
  .net-weight {
    position: absolute;
    left: 13px;
    top: 276px;
    color: var(--gold);
    font-family: "Gelasio", Georgia, serif;
    font-size: 12px;
    letter-spacing: 0.3px;
  }
</style>
</head>
<body>
<main class="label-sheet">
  <section class="label label--mocha">
    <div class="label__card">
      <h1 class="brand"><span class="brand__name">Harlan Wick</span><span class="brand__line">chocolates</span></h1>
      <div class="flavour-band">
        <h2 class="flavour-name">Cafe Mocha</h2>
        <p class="flavour-desc">Exclusive Hand-Crafted<br>Chocolate Bar<br>with Truffle filling</p>
      </div>
      <div class="bar-visual" role="img" aria-label="Milk chocolate bar broken into squares"></div>
      <p class="net-weight">NET WT. 2,5 OZ / 70 G</p>
    </div>
  </section>

  <section class="label label--ember">
    <div class="label__card">
      <h1 class="brand"><span class="brand__name">Harlan Wick</span><span class="brand__line">chocolates</span></h1>
      <div class="flavour-band">
        <h2 class="flavour-name">Velmora Ember</h2>
        <p class="flavour-desc">Exclusive Hand-Crafted<br>Chocolate Bar<br>with Truffle filling</p>
      </div>
      <div class="bar-visual" role="img" aria-label="Milk chocolate bar broken into squares"></div>
      <p class="net-weight">NET WT. 2,5 OZ / 70 G</p>
    </div>
  </section>

  <section class="label label--pumpkin">
    <div class="label__card">
      <h1 class="brand"><span class="brand__name">Harlan Wick</span><span class="brand__line">chocolates</span></h1>
      <div class="flavour-band">
        <h2 class="flavour-name">Pumpkin Pie</h2>
        <p class="flavour-desc">Exclusivelylyly Hand-Crafted<br>Chocolate Bar<br>with Truffle filling</p>
      </div>
      <div class="bar-visual" role="img" aria-label="Milk chocolate bar broken into squares"></div>
      <p class="net-weight">NET WT. 2,5 OZ / 70 G</p>
    </div>
  </section>
</main>
</body>
</html>
```